Site for entrepreneurs/small businesses needs Logo, Homepage

Looking for a logo, either an icon, or stylized text, or a combination of both, and a home page design which fits with it. The logo will be for use on the public website as well as for printed collateral (business cards, post cards, brochures and various other marketing materials).

The site is called Orbitwell (Orbitwell.example). This is to be a national, and eventually an international brand. The new service will provide an easy-to-use platform for entrepreneurs to build their business and web presence together in an integrated way which allows them to focus on their core competency.

The site/service will be dead-simple to use, A/B/C, 1/2/3. We will want some sort of "Get started for FREE" promotional space to collect the person's email address with multiple points of interest which guide the user back to this one call to action: sign up for free. We will feature editorial/blog stories, customer testimonials, and present several key features the the reader just can't live without if they are starting a new business.

Criteria:
* Refer to our comparable sites/logos in the design document attached
* Incorporate our color scheme (but complementary colors welcome)
* No Serif fonts!
* No photo-realistic elements for logo
* Logo must present well in gray scale and/or black/white (for printed materials)
* Strokes/borders that are wider to promote simplicity (vs. thin/precise lines which promote technical complexity)

Inspirations:
* Creative/Custom (but legible) fonts
* Excitement, energetic, jumping for joy
* Karate / Ninja / Power / Precision
* Dance Moves
* Regional influences: California, Silicon Valley, West Coast, Surf City, Beaches, Sunset
* Simple/easy, no-brainer solutions

Target Market(s)

Small Businesses / Entrepreneurs

Logo Text

Orbitwell or Orbitwell.example

Number of Pages Required

1 page

Font styles to use
Sans Serif
Decorative

Requirements
Must have
• See the attached style guide (PDF)

```html
<!DOCTYPE html>
<html lang="en">
<head>
<meta charset="utf-8">
<title>Orbitwell — Get started for free</title>
<link href="https://fonts.googleapis.com/css2?family=Exo+2:wght@400;500;600;700;800&display=swap" rel="stylesheet">
<style>
:root{
  --purple:#7d12cc;
  --purple-deep:#3e0a78;
  --purple-night:#1c0540;
  --ink:#3a0a6c;
  --text:#3d3d46;
  --white:#ffffff;
  --grey:#f3f3f6;
  --footer-bar:#2b0a56;
  --input-border:#d9c9ef;
  --sky:#9cc6fb;
  --sky-deep:#4f8fe8;
  --lilac:#b58af0;
}
*{margin:0;padding:0;box-sizing:border-box}
html,body{width:1200px;height:3169px;overflow:hidden}
body{position:relative;background:var(--white);font-family:"Exo 2",Arial,sans-serif;color:var(--text)}
.backdrop{position:absolute;left:0;top:0;width:1200px;height:3169px}
.abs{position:absolute}

/* header */
.brand{left:76px;top:18px;display:flex;align-items:center;gap:12px}
.brand-dot{width:72px;height:72px;border-radius:50%;background:var(--purple-night)}
.brand-name{font-size:36px;font-weight:700;color:var(--white);letter-spacing:-0.3px}
.main-nav{top:37px;left:0;width:1200px;height:20px}
.main-nav a{position:absolute;top:0;color:var(--white);text-decoration:none;font-size:14px;font-weight:500;letter-spacing:.6px;text-transform:uppercase;white-space:nowrap}
.main-nav a:nth-child(1){left:448px}
.main-nav a:nth-child(2){left:554px}
.main-nav a:nth-child(3){left:708px}
.main-nav a:nth-child(4){left:932px}
.main-nav a:nth-child(5){left:1035px}

/* hero signup */
.signup{left:108px;top:228px;width:317px}
.signup h1{font-size:28px;font-weight:700;color:var(--white);letter-spacing:.3px;margin-bottom:18px;text-align:center;text-transform:uppercase;white-space:nowrap}
.field{display:block;width:317px;height:48px;border-radius:24px;background:var(--white);border:2px solid var(--input-border);padding:0 24px;font-size:15px;font-weight:600;color:#8a7aa6;line-height:44px;margin-bottom:19px;text-transform:uppercase}
.btn{display:inline-block;border-radius:26px;background:var(--purple-deep);color:var(--white);font-weight:700;text-transform:uppercase;letter-spacing:.4px;text-align:center;box-shadow:0 0 0 3px rgba(155,40,230,.55);white-space:nowrap}
.signup .btn{margin-left:63px;width:190px;height:50px;line-height:50px;font-size:16px}

/* blog */
.blog{left:663px;top:786px;width:400px}
.section-title{font-weight:700;font-size:42px;letter-spacing:.5px;text-transform:uppercase;white-space:nowrap}
.blog .section-title{color:var(--ink)}
.blog p{margin-top:12px;font-size:15.5px;line-height:23.5px;text-align:justify;color:var(--text)}
.post-meta{display:flex;gap:26px;margin-top:16px;font-size:14px;color:var(--purple)}
.post-meta span{display:flex;align-items:center;gap:8px}
.blog .btn{margin-top:30px;margin-left:-4px;width:182px;height:58px;line-height:58px;font-size:16px}

/* features */
.features-title{top:1452px;left:0;width:1200px;text-align:center;color:var(--white)}
.feature{color:var(--white);width:440px}
.feature h3{font-size:23px;font-weight:700;margin-bottom:6px}
.feature p{font-size:16.5px;line-height:24px}
.feature-art{border-radius:50%;width:314px;height:314px;
  background:radial-gradient(circle at 50% 50%,var(--sky-deep) 0%,var(--sky) 28%,#dcebff 50%,#ffffff 70%)}

/* testimonials */
.testimonial{left:118px;top:2470px;width:360px;color:var(--white)}
.testimonial blockquote{margin-top:14px;font-size:14.5px;line-height:24px}
.testimonial cite{display:block;margin-top:12px;font-style:normal;font-weight:700;font-size:24px}
.dots{left:388px;top:2682px;display:flex;gap:9px}
.dots i{width:14px;height:14px;border-radius:50%;background:var(--purple-night)}

/* footer */
.footer-col h4{font-size:24px;font-weight:700;color:var(--ink);text-transform:uppercase;margin-bottom:14px}
.footer-col ul{list-style:none}
.footer-col li{font-size:15px;line-height:33px;color:#2a2a33;display:flex;align-items:center;gap:14px;white-space:nowrap}
.social-dot{width:12px;height:12px;border-radius:50%;background:#222}
.contact li{align-items:flex-start}
.contact svg{flex:none;margin-top:9px}
.footer-bar{left:0;top:3110px;width:1200px;height:59px;background:var(--footer-bar);color:var(--white);text-align:center;line-height:59px;font-size:14.5px}
</style>
</head>
<body>

<svg class="backdrop" viewBox="0 0 1200 3169" aria-hidden="true">
  <defs>
    <linearGradient id="heroGrad" x1="0" y1="0" x2="1" y2="0.4">
      <stop offset="0" stop-color="#3e0a78"/>
      <stop offset="1" stop-color="#8a14d8"/>
    </linearGradient>
    <linearGradient id="bandGrad" x1="0" y1="0" x2="0" y2="1">
      <stop offset="0" stop-color="#6c0fc0"/>
      <stop offset="1" stop-color="#7e12cc"/>
    </linearGradient>
  </defs>
  <path fill="url(#heroGrad)" d="M0 0H1200V690C1000 720 760 640 560 665C420 690 300 730 170 700C90 680 30 660 0 650Z"/>
  <path fill="#ffffff" d="M760 95C900 60 1100 80 1170 130C1215 170 1205 560 1175 615C1110 690 900 700 700 660C540 625 425 520 450 400C475 280 620 130 760 95Z"/>
  <rect fill="#f3f3f6" x="0" y="2560" width="1200" height="560"/>
  <path fill="url(#bandGrad)" d="M0 1440C250 1432 440 1370 590 1245C730 1130 950 1058 1200 1055V2450H900L640 2720C520 2780 300 2770 0 2720Z"/>
  <path fill="#ffffff" d="M560 2600C600 2455 760 2400 900 2395C1050 2390 1150 2398 1200 2410V2842H780C650 2830 535 2730 560 2600Z"/>
</svg>

<header>
  <div class="abs brand"><span class="brand-dot"></span><span class="brand-name">Orbitwell</span></div>
  <nav class="abs main-nav">
    <a href="#about">About us</a>
    <a href="#blog">Our blog story</a>
    <a href="#testimonials">Customer testimonials</a>
    <a href="#features">Features</a>
    <a href="#contact">Contact us</a>
  </nav>
</header>

<div class="abs" role="img" aria-label="Isometric illustration of a team meeting around a dashboard screen with charts" style="left:560px;top:120px;width:590px;height:520px;border-radius:46% 40% 42% 48%;background:radial-gradient(ellipse at 50% 35%,#c9d3f2 0%,#dfe3f4 30%,#eceef8 52%,#ffffff 74%)"></div>

<section class="abs signup" id="about">
  <h1>Get started for free</h1>
  <div class="field">Name</div>
  <div class="field">Email ID</div>
  <a class="btn">Sign up for free</a>
</section>

<svg class="abs" style="left:0;top:760px" width="600" height="600" viewBox="0 760 600 600" role="img" aria-label="Isometric illustration of a person working at a computer desk">
  <defs>
    <radialGradient id="deskGrad" cx="0.45" cy="0.45" r="0.7">
      <stop offset="0" stop-color="#d21ee8"/>
      <stop offset="0.45" stop-color="#8a18e2"/>
      <stop offset="1" stop-color="#4a14c8"/>
    </radialGradient>
  </defs>
  <path fill="url(#deskGrad)" d="M0 830C150 790 390 795 505 855C600 905 580 1110 520 1225C470 1320 330 1362 225 1325C125 1290 60 1210 0 1190Z"/>
  <ellipse cx="95" cy="1200" rx="46" ry="36" fill="#2d0a7a"/>
</svg>

<section class="abs blog" id="blog">
  <h2 class="section-title">Blog Stories</h2>
  <p>Donec nisl et mi auctor potenti id metus ipsum. Molestie phasellus proin vehicula maecenas sem nunc congue tincidunt. Vestibulum magnis magna rutrum animi vitae. At id nisl. Porta proin integer tortor quia fringilla. Luctus mauris nec. Magna tortor ullamcorper est massa eu. Tristique erat sed. Ultricies arcu quam</p>
  <div class="post-meta">
    <span><svg width="18" height="16" viewBox="0 0 18 16"><path d="M9 15L2 8.5A4 4 0 0 1 9 3a4 4 0 0 1 7 5.5Z" fill="none" stroke="currentColor" stroke-width="2"/></svg>12 people like</span>
    <span><svg width="16" height="17" viewBox="0 0 16 17"><rect x="1" y="3" width="14" height="13" rx="1.5" fill="none" stroke="currentColor" stroke-width="2"/><path d="M1 7H15M5 1V4M11 1V4" stroke="currentColor" stroke-width="2"/></svg>23-05-2018</span>
    <span><svg width="16" height="17" viewBox="0 0 16 17"><circle cx="8" cy="5" r="4" fill="none" stroke="currentColor" stroke-width="2"/><path d="M1 16C1 11 15 11 15 16" fill="none" stroke="currentColor" stroke-width="2"/></svg>By Mara</span>
  </div>
  <a class="btn">More stories</a>
</section>

<h2 class="abs section-title features-title" id="features">Key Features</h2>

<div class="abs feature-art" role="img" aria-label="Illustration of people assembling puzzle pieces" style="left:104px;top:1485px"></div>
<div class="abs feature" style="left:617px;top:1556px">
  <h3>Team Work</h3>
  <p>Lorem magna volutpat. Ullam neque lobortis. Feugiat vitae at. Suscipit vestibulum non venenatis sollicitudin metus scelerisque wisi orci imperdiet vitae risus quisque eget in.</p>
</div>

<div class="abs feature-art" role="img" aria-label="Illustration of people with charts on a large phone" style="left:809px;top:1756px"></div>
<div class="abs feature" style="left:226px;top:1862px">
  <h3>Business Statistics</h3>
  <p>Lorem magna volutpat. Ullam neque lobortis. Feugiat vitae at. Vel sem laoreet numquam tellus rutrum phasellus massa culpa dis duis adipiscing</p>
</div>

<div class="abs feature-art" role="img" aria-label="Illustration of a crowd gathered around a megaphone" style="left:106px;top:2043px"></div>
<div class="abs feature" style="left:497px;top:2082px">
  <h3>Marketing</h3>
  <p>Lorem magna volutpat. Ullam neque lobortis. Feugiat vitae at. Suscipit vestibulum non venenatis sollicitudin metus scelerisque wisi orci imperdiet vitae risus quisque eget in.</p>
</div>

<div class="abs" role="img" aria-label="Illustration of people around a laptop with documents, a clock and a pencil" style="left:630px;top:2420px;width:550px;height:400px;border-radius:50%;background:radial-gradient(ellipse at 50% 55%,#8a3ee0 0%,var(--lilac) 28%,#e3d3fa 52%,#ffffff 72%)"></div>

<section class="abs testimonial" id="testimonials">
  <h2 class="section-title">Testimonials</h2>
  <blockquote>"Donec nisl et mi auctor potenti id metus ipsum. Molestie phasellus proin vehicula maecenas sem nunc congue tincidunt. Vestibulum magnis magna rutrum animi vitae"</blockquote>
  <cite>- Nora Vale</cite>
</section>
<div class="abs dots"><i></i><i></i><i></i></div>

<footer>
  <div class="abs footer-col" style="left:78px;top:2874px">
    <h4>Links</h4>
    <ul>
      <li>Home</li><li>About Us</li><li>Our Blog Stories</li><li>Key Features</li><li>Customer Testimonials</li>
    </ul>
  </div>
  <div class="abs footer-col" style="left:292px;top:2919px">
    <ul><li>Login</li><li>Sign Up</li></ul>
  </div>
  <div class="abs footer-col" style="left:535px;top:2874px">
    <h4>Follow us</h4>
    <ul>
      <li><span class="social-dot"></span>Friendnest</li>
      <li><span class="social-dot"></span>Chirpline</li>
      <li><span class="social-dot"></span>Workgrid</li>
      <li><span class="social-dot"></span>Snapframe</li>
    </ul>
  </div>
  <div class="abs footer-col contact" id="contact" style="left:864px;top:2874px">
    <h4>Contact us</h4>
    <ul>
      <li><svg width="14" height="18" viewBox="0 0 14 18"><path d="M7 17C7 17 1 10 1 6.5A6 6 0 0 1 13 6.5C13 10 7 17 7 17Z" fill="#222"/><circle cx="7" cy="6.5" r="2.2" fill="#f3f3f6"/></svg><span>#123, Lorium ipsum,<br>Dolor Amit,<br>City.</span></li>
      <li><svg width="16" height="16" viewBox="0 0 16 16"><path d="M3 1L6 4L4.5 6C5.5 8 8 10.5 10 11.5L12 10L15 13L13 15C7 15 1 9 1 3Z" fill="#222"/></svg>0800-555 0142</li>
      <li><svg width="18" height="14" viewBox="0 0 18 14"><rect x="0" y="0" width="18" height="14" rx="1.5" fill="#222"/><path d="M1 1L9 8L17 1" fill="none" stroke="#f3f3f6" stroke-width="1.6"/></svg>support@orbitwell.example</li>
    </ul>
  </div>
  <div class="abs footer-bar">Copyright © 2018 . www.orbitwell.example</div>
</footer>

</body>
</html>
```